MRT Property - Business Cards

Looking for a business card & general letterhead, signage etc design for our new logo.

Colours:
000a20
0056a2
00b5ef
0088ce
68cef2

Fonts:
Poppins
Karla

Please keep look and feel of new brand - example in the zip package I sent.

```html
<!DOCTYPE html>
<html lang="en">
<head>
<meta charset="utf-8">
<title>MRT Property – Business Cards</title>
<link href="https://fonts.googleapis.com/css2?family=Poppins:wght@500;600;700&family=Karla:wght@400;500&display=swap" rel="stylesheet">
<style>
  :root {
    --navy: #000a20;
    --card-navy: #0b1020;
    --royal: #0056a2;
    --royal-deep: #1a3a78;
    --sky: #00b5ef;
    --ocean: #0088ce;
    --ice: #68cef2;
    --white: #ffffff;
    --backdrop: #e9ecf1;
  }
  * { margin: 0; padding: 0; box-sizing: border-box; }
  html, body {
    width: 1200px;
    height: 880px;
    overflow: hidden;
    background: var(--backdrop);
  }
  .sheet {
    width: 1200px;
    height: 880px;
    display: flex;
    flex-direction: column;
    align-items: center;
    justify-content: center;
    gap: 34px;
  }
  .card {
    position: relative;
    width: 700px;
    height: 400px;
    border-radius: 34px;
    overflow: hidden;
    box-shadow: 0 10px 26px rgba(0, 10, 32, 0.18);
  }

  /* Front */
  .card-front {
    background: var(--royal);
    display: flex;
    align-items: center;
    justify-content: center;
  }
  .front-mark {
    display: flex;
    align-items: center;
    gap: 26px;
    font-family: "Poppins", sans-serif;
    font-weight: 700;
    font-size: 74px;
    letter-spacing: 1px;
    color: var(--royal-deep);
  }
  .front-mark .dot {
    width: 70px;
    height: 70px;
    border-radius: 50%;
    background: #2f74bd;
  }

  /* Back */
  .card-back {
    background: var(--card-navy);
    font-family: "Karla", sans-serif;
    color: var(--white);
  }
  .brand {
    position: absolute;
    left: 56px;
    top: 70px;
    display: flex;
    align-items: center;
    gap: 16px;
    font-family: "Poppins", sans-serif;
    font-weight: 700;
    font-size: 44px;
    color: var(--royal);
  }
  .brand .dot {
    width: 46px;
    height: 46px;
    border-radius: 50%;
    background: var(--ocean);
  }
  .holder {
    position: absolute;
    right: 58px;
    top: 58px;
    text-align: right;
  }
  .holder-name {
    font-family: "Poppins", sans-serif;
    font-weight: 600;
    font-size: 23px;
    letter-spacing: 1.5px;
    color: var(--royal);
    line-height: 1.2;
  }
  .holder-role {
    font-size: 17px;
    color: var(--white);
    margin-top: 2px;
  }
  .accent-bar {
    position: absolute;
    right: 28px;
    top: 56px;
    width: 10px;
    height: 60px;
    background: var(--royal);
  }
  .address {
    position: absolute;
    left: 56px;
    top: 232px;
    font-size: 17px;
    line-height: 1.4;
    letter-spacing: 0.4px;
  }
  .contacts {
    position: absolute;
    left: 56px;
    top: 300px;
    list-style: none;
    font-size: 17px;
    letter-spacing: 0.4px;
  }
  .contacts li {
    display: flex;
    align-items: center;
    gap: 10px;
    height: 24px;
  }
  .contacts svg {
    width: 15px;
    height: 15px;
    flex: none;
  }
</style>
</head>
<body>
<main class="sheet">

  <section class="card card-front" aria-label="Business card front">
    <div class="front-mark">
      <span class="dot"></span>
      <span>MRT Property</span>
    </div>
  </section>

  <section class="card card-back" aria-label="Business card back">
    <div class="brand">
      <span class="dot"></span>
      <span>MRT Property</span>
    </div>

    <div class="holder">
      <p class="holder-name">DANIEL REED</p>
      <p class="holder-role">Managing Director</p>
    </div>
    <span class="accent-bar"></span>

    <p class="address">Your address, City<br>State, Zip 1234</p>

    <ul class="contacts">
      <li>
        <svg viewBox="0 0 24 24" aria-hidden="true"><path fill="#00b5ef" d="M6.6 10.8a15.1 15.1 0 0 0 6.6 6.6l2.2-2.2a1 1 0 0 1 1-.25 11.4 11.4 0 0 0 3.6.57 1 1 0 0 1 1 1V20a1 1 0 0 1-1 1A17 17 0 0 1 3 4a1 1 0 0 1 1-1h3.5a1 1 0 0 1 1 1c0 1.25.2 2.45.57 3.57a1 1 0 0 1-.25 1z"/></svg>
        <span>123 456 789</span>
      </li>
      <li>
        <svg viewBox="0 0 24 24" aria-hidden="true"><rect x="2" y="5" width="20" height="14" rx="2" fill="#00b5ef"/><path d="M3 6l9 7 9-7" stroke="#0b1020" stroke-width="1.8" fill="none"/></svg>
        <span>info@yourgmail.com</span>
      </li>
      <li>
        <svg viewBox="0 0 24 24" aria-hidden="true"><circle cx="12" cy="12" r="10" fill="#00b5ef"/><path d="M2 12h20M12 2c3 3 3 17 0 20M12 2c-3 3-3 17 0 20" stroke="#0b1020" stroke-width="1.4" fill="none"/></svg>
        <span>www.yourwebsite.com</span>
      </li>
    </ul>
  </section>

</main>
</body>
</html>
```